A clean crisp business card for a Landscape Construction company. Designed to be easy to read contact/ info and also be appealing/interesting, unlike a traditional business card.

Industry/Entity Type

Landscape Construction

Contact Information for Business Card

Company name : Brambleford Landscape Construction, phone number: (877) 62Vista, website:Bramblefordyards.example, Email, sales@bramblefordyards.example

Requirements
Nice to have
• Luxurious finishes/ details…. Icons or emblems next to contact info
Should not have
• Clipart or general pictures

```html
<!DOCTYPE html>
<html lang="en">
<head>
<meta charset="utf-8">
<title>Brambleford Landscape Construction – Business Card</title>
<link href="https://fonts.googleapis.com/css2?family=Cinzel:wght@600&family=Noto+Sans:wght@400;500&display=swap" rel="stylesheet">
<style>
  :root{
    --page:#b4b8ba;
    --card-dark:#1f1f1f;
    --card-dark-hi:#3a3a3a;
    --white:#ffffff;
    --blue:#2a6bbf;
    --green:#8dc63f;
    --ink:#1e1e1e;
  }
  html,body{margin:0;padding:0;overflow:hidden}
  body{
    width:1200px;height:928px;background:var(--page);
    position:relative;font-family:"Noto Sans",sans-serif;
  }
  .card{
    position:absolute;left:262px;width:676px;height:386px;
    border-radius:18px;overflow:hidden;
  }
  .card--back{top:56px;background:var(--card-dark)}
  .card--front{top:484px;background:var(--white)}

  .back-pattern{
    position:absolute;inset:0;
    background:linear-gradient(90deg,var(--card-dark) 0%,#242424 45%,var(--card-dark-hi) 100%);
  }
  .back-name{
    position:absolute;left:0;right:0;top:176px;text-align:center;
    font-family:"Cinzel",serif;font-weight:600;font-size:26px;
    color:var(--green);letter-spacing:1px;
  }

  .brand{
    position:absolute;left:40px;top:78px;width:250px;
    font-family:"Cinzel",serif;font-weight:600;font-size:25px;line-height:1.15;
    color:var(--blue);
  }
  .holder{position:absolute;right:40px;top:112px;text-align:right}
  .holder__name{
    font-family:"Cinzel",serif;font-weight:600;font-size:28px;
    color:var(--blue);letter-spacing:1px;margin:0;
  }
  .holder__role{font-size:16px;color:var(--ink);margin-top:4px}

  .contacts{position:absolute;left:42px;top:216px;margin:0;padding:0;list-style:none}
  .contacts li{
    display:flex;align-items:center;gap:8px;
    font-size:16px;color:var(--ink);height:26px;
  }
  .contacts svg{width:16px;height:16px;flex:none}

  .wave{position:absolute;left:0;top:0;width:676px;height:386px}
  .address{
    position:absolute;right:40px;top:310px;text-align:right;
    color:var(--white);font-size:16px;font-weight:500;line-height:27px;
  }
</style>
</head>
<body>

<section class="card card--back">
  <div class="back-pattern" role="img" aria-label="Repeating brand emblem pattern fading from black to silver"></div>
  <div class="back-name">Brambleford</div>
</section>

<section class="card card--front">
  <svg class="wave" viewBox="0 0 676 386" aria-hidden="true">
    <path d="M0 272 C70 330 150 362 260 352 C400 338 520 272 676 280 L676 386 L0 386 Z" fill="var(--blue)"/>
    <path d="M28 286 C100 340 170 362 270 350 C410 332 520 260 660 268" fill="none" stroke="var(--white)" stroke-width="9"/>
    <path d="M28 286 C100 340 170 362 270 350 C410 332 520 260 660 268" fill="none" stroke="var(--green)" stroke-width="4"/>
  </svg>

  <div class="brand">Brambleford Landscape Construction</div>

  <div class="holder">
    <p class="holder__name">Daniel Harlow</p>
    <div class="holder__role">Director</div>
  </div>

  <ul class="contacts">
    <li>
      <svg viewBox="0 0 24 24"><path fill="var(--green)" d="M6.6 10.8a15.1 15.1 0 0 0 6.6 6.6l2.2-2.2a1 1 0 0 1 1-.25 11.4 11.4 0 0 0 3.6.6 1 1 0 0 1 1 1V20a1 1 0 0 1-1 1A17 17 0 0 1 3 4a1 1 0 0 1 1-1h3.5a1 1 0 0 1 1 1c0 1.25.2 2.45.6 3.6a1 1 0 0 1-.25 1z"/></svg>
      (877) 62Vista
    </li>
    <li>
      <svg viewBox="0 0 24 24"><rect x="2" y="5" width="20" height="14" rx="1.5" fill="var(--green)"/><path d="M3 6.5l9 6.5 9-6.5" fill="none" stroke="var(--white)" stroke-width="1.6"/></svg>
      sales@bramblefordyards.example
    </li>
    <li>
      <svg viewBox="0 0 24 24"><circle cx="12" cy="12" r="10" fill="var(--green)"/><path d="M2 12h20M12 2c3 3 3 17 0 20M12 2c-3 3-3 17 0 20" fill="none" stroke="var(--white)" stroke-width="1.3"/></svg>
      www.bramblefordyards.example
    </li>
  </ul>

  <div class="address">
    4170 Alder Creek Rd<br>
    NUM 118, Millbrook, OH 45099
  </div>
</section>

</body>
</html>
```